Construction company business card

One side to be the logo with the company name, The other side I would like: (Tomas verbick) Project manager 41 barrow crescent kelmore 52917306224783(03) 9703 2428Info@gudeljgroup.comAnd then maybe a couple dot points saying what we do:Construction (commercial & industrial) Civil construction

Anything else please contact me!
Maybe curved st one edge of the card

Target Market(s)

Older clientele

Industry/Entity Type

Construction Company

Contact Information for Business Card

Read above

Colors
3277b5
1b1b1b
9d9d9d

Requirements
Must have
• Use my logo on one side
Nice to have
• Read above
Should not have
• Read above

```html
<!DOCTYPE html>
<html lang="en">
<head>
<meta charset="utf-8">
<title>Ridgeway Construction – Business Card</title>
<link rel="stylesheet" href="https://fonts.googleapis.com/css2?family=Open+Sans:wght@400;600;800&display=swap">
<style>
  :root {
    --brand-blue: #1158a8;
    --ink-dark: #1b1b1b;
    --ink-grey: #4a4a4a;
    --rule-grey: #9d9d9d;
    --stripe-grey: #444444;
    --paper: #ffffff;
    --backdrop: #3a3b3d;
  }
  * { box-sizing: border-box; margin: 0; padding: 0; }
  html, body { width: 1200px; height: 900px; overflow: hidden; }
  body {
    background: var(--backdrop);
    font-family: "Open Sans", Arial, sans-serif;
    display: flex;
    flex-direction: column;
    align-items: center;
    justify-content: center;
    gap: 40px;
  }
  .card {
    position: relative;
    width: 680px;
    height: 388px;
    border-radius: 26px;
    overflow: hidden;
    box-shadow: 0 10px 26px rgba(0,0,0,0.45);
  }

  /* Front */
  .card-front {
    background: var(--brand-blue);
    display: flex;
    align-items: center;
    justify-content: center;
  }
  .brand { display: flex; align-items: center; gap: 18px; }
  .brand-dot {
    width: 54px; height: 54px; border-radius: 50%;
    background: var(--paper);
  }
  .brand-name {
    color: var(--paper);
    font-weight: 800;
    font-size: 40px;
    line-height: 1.05;
    letter-spacing: 1px;
  }
  .brand-name .sub { display: block; font-size: 17px; letter-spacing: 9px; }

  /* Back */
  .card-back { background: var(--paper); }
  .back-brand {
    position: absolute; left: 56px; top: 72px;
    display: flex; align-items: center; gap: 12px;
  }
  .back-brand .brand-dot { width: 36px; height: 36px; background: var(--brand-blue); }
  .back-brand .brand-name { color: var(--brand-blue); font-size: 27px; }
  .back-brand .brand-name .sub { font-size: 11.5px; letter-spacing: 6px; }

  .person {
    position: absolute; right: 44px; top: 140px; text-align: right;
  }
  .person-name { color: var(--brand-blue); font-weight: 800; font-size: 22px; line-height: 1.1; }
  .person-title { color: var(--ink-grey); font-size: 14px; }

  .divider {
    position: absolute; left: 165px; right: 40px; top: 202px;
    height: 1px; background: var(--rule-grey);
  }

  .details {
    position: absolute; right: 44px; top: 214px; text-align: right;
    color: var(--ink-grey); font-size: 13.5px; line-height: 1.35;
  }
  .services { list-style: none; margin-top: 6px; font-size: 12.5px; line-height: 1.6; }
  .services li::after {
    content: ""; display: inline-block; width: 6px; height: 6px;
    border-radius: 50%; background: var(--brand-blue);
    margin-left: 8px; vertical-align: middle;
  }

  .contact {
    position: absolute; left: 58px; top: 228px; list-style: none;
    color: var(--ink-grey); font-size: 15px; line-height: 1.75;
  }
  .contact li { display: flex; align-items: center; gap: 10px; }
  .contact svg { width: 14px; height: 14px; fill: var(--brand-blue); }

  .edge-bands { position: absolute; left: 0; bottom: 0; width: 680px; height: 388px; }
  .edge-bands .band-blue { fill: var(--brand-blue); }
  .edge-bands .band-grey { fill: var(--stripe-grey); }
</style>
</head>
<body>

<section class="card card-front" aria-label="Card front">
  <div class="brand">
    <span class="brand-dot"></span>
    <div class="brand-name">RIDGEWAY<span class="sub">CONSTRUCTION</span></div>
  </div>
</section>

<section class="card card-back" aria-label="Card back">
  <svg class="edge-bands" viewBox="0 0 680 388" aria-hidden="true">
    <path class="band-grey" d="M0,343 L418,343 L409,352 L0,352 Z"/>
    <path class="band-blue" d="M0,360 L404,360 C432,360 436,304 474,304 L680,304 L680,388 L0,388 Z"/>
  </svg>

  <div class="back-brand">
    <span class="brand-dot"></span>
    <div class="brand-name">RIDGEWAY<span class="sub">CONSTRUCTION</span></div>
  </div>

  <div class="person">
    <p class="person-name">Tomas verbick</p>
    <p class="person-title">Project manager</p>
  </div>

  <div class="divider"></div>

  <div class="details">
    <p>41 barrow crescent kelmore</p>
    <p>52917306224783</p>
    <ul class="services">
      <li>Civil construction</li>
      <li>Construction (commercial &amp; industrial)</li>
    </ul>
  </div>

  <ul class="contact">
    <li>
      <svg viewBox="0 0 24 24"><path d="M6.6 10.8a15.1 15.1 0 0 0 6.6 6.6l2.2-2.2c.3-.3.7-.4 1-.2 1.1.4 2.3.6 3.6.6.6 0 1 .4 1 1V20c0 .6-.4 1-1 1A17 17 0 0 1 3 4c0-.6.4-1 1-1h3.5c.6 0 1 .4 1 1 0 1.3.2 2.5.6 3.6.1.3 0 .7-.2 1z"/></svg>
      <span>(03) 9418 6573</span>
    </li>
    <li>
      <svg viewBox="0 0 24 24"><path d="M2 5h20v14H2z M4 7v.4l8 5.2 8-5.2V7z" fill-rule="evenodd"/></svg>
      <span>Info@verbickgroup.com</span>
    </li>
    <li>
      <svg viewBox="0 0 24 24"><path d="M12 2a10 10 0 1 0 0 20 10 10 0 0 0 0-20zm-1 17.9A8 8 0 0 1 4.1 10L9 15v1a2 2 0 0 0 2 2zm6.9-2.5A2 2 0 0 0 16 16h-1v-3a1 1 0 0 0-1-1H8v-2h2a1 1 0 0 0 1-1V7h2a2 2 0 0 0 2-2v-.4a8 8 0 0 1 2.9 12.8z"/></svg>
      <span>www.verbickgroup.com</span>
    </li>
  </ul>
</section>

</body>
</html>
```